Ridge Lass Crew (Flyer)

I want a flyer to advertise my service.
Details below, and logo's to use are attached.

A girls only after school program, 11-14yrs, as OSHC is no longer avail, dedicated to coaching & mentoring our girls into strong, independent young women.

The Brainchild of Rebecca Folwin, Ridge Lass Crew was created to address the growing demand for after school/school holiday supervision for kids moving from primary into high school, when OSHC ceases to exist.
With over 12 years experience mentoring and coaching young women in the corporate world, Bec decided to leave her role as a Director with Tarrant Trust, and follow her passion.
Bec, along with her sister Lorraine, who has over 10 years experience in local communities as a Youth Worker, and is also a qualified Enrolled Nurse, embarked on building a program designed to keep parents happy (by knowing their girls are safe) and dedicated to coaching and mentoring our girls into strong, independent young women.
Open every afternoon and during school holidays, we look to offer;
- Daily meditation
- Healthy snacks
- Dedicated homework time
- Organised group activity, led by qualified instructors (yoga, fitness class, soccer etc)
- Regular guests speakers, addressing issues/concerns for young people today
- SOCIAL MEDIA FREE ZONE

Located 87 Pelham Pde, Carrowby Heights (across from Crestmoor Day Clinic)
Open 3-6pm Monday to Friday

Facebook page: http://fb.example/ridgelasscrew
Email: info@ridgelasscrew.example.au
Mobile: 0455817396

Target Market(s)

Parents of teenage girls, teenage girls 11-14 years

Industry/Entity Type

School

Font styles to use
Sans Serif

Colors
b768aa
e667a6

Requirements
Must have
• What progam is - see brief
• Who runs it
Should not have
• Not be too busy, not overly mature images

```html
<!DOCTYPE html>
<html lang="en">
<head>
<meta charset="utf-8">
<title>Ridge Lass Crew – After School Program Flyer</title>
<link href="https://fonts.googleapis.com/css2?family=Bree+Serif&family=Cinzel:wght@700&family=Libre+Baskerville:ital@1&family=Open+Sans:wght@400;600;700&family=Roboto+Condensed:wght@400;700&display=swap" rel="stylesheet">
<style>
  :root {
    --purple: #b768aa;
    --purple-deep: #9b2fc0;
    --purple-glow: #c85be0;
    --pink: #e667a6;
    --panel: #b36aa8;
    --ink: #1d1418;
    --white: #ffffff;
    --logo-pink: #e4457f;
  }
  * { margin: 0; padding: 0; box-sizing: border-box; }
  html, body { width: 848px; height: 1200px; overflow: hidden; background: var(--white); }
  .flyer { position: relative; width: 848px; height: 1200px; overflow: hidden; background: var(--purple); font-family: "Open Sans", sans-serif; color: var(--ink); }

  .hero { position: absolute; left: 0; top: 0; width: 848px; height: 486px;
    background: radial-gradient(ellipse at 50% 45%, var(--purple-glow) 0%, var(--purple-deep) 70%, #7b1f9a 100%); }

  .brand-card { position: absolute; left: 32px; top: 36px; width: 260px; height: 360px; background: var(--white);
    display: flex; align-items: center; justify-content: center; text-align: center; }
  .brand-card span { font-family: "Open Sans", sans-serif; font-weight: 700; font-size: 34px; line-height: 1.15; color: var(--logo-pink); }

  .program-panel { position: absolute; left: 412px; top: 62px; width: 388px; height: 330px; background: var(--panel);
    border-radius: 12px; text-align: center; color: var(--white); padding-top: 42px; }
  .program-panel h1 { font-family: "Bree Serif", serif; font-weight: 400; font-size: 43px; line-height: 1.5; }
  .program-panel .ages { font-family: "Open Sans", sans-serif; font-weight: 700; font-size: 60px; line-height: 1.25; margin-top: 8px; }
  .program-panel .note { font-family: "Open Sans", sans-serif; font-weight: 700; font-size: 21px; color: var(--ink); margin-top: 22px; }

  .founder-band { position: absolute; left: 0; top: 486px; width: 848px; height: 124px; background: var(--pink);
    text-align: center; padding-top: 13px; }
  .founder-band p { font-family: "Open Sans", sans-serif; font-weight: 700; font-size: 40px; line-height: 50px; color: var(--ink); }

  .offer { position: absolute; left: 0; top: 610px; width: 848px; height: 476px; }
  .offer h2 { position: absolute; left: 0; width: 816px; top: 48px; text-align: center; font-family: "Cinzel", serif;
    font-weight: 700; font-size: 36px; font-variant: small-caps; color: var(--ink); }
  .offer-list { position: absolute; left: 26px; top: 92px; list-style: none; }
  .offer-list li { position: relative; padding-left: 32px; font-family: "Libre Baskerville", serif; font-style: italic;
    font-size: 25px; color: var(--white); height: 42px; line-height: 42px; -webkit-text-stroke: 0.4px var(--white); }
  .offer-list li.wrap { height: auto; line-height: 42px; }
  .offer-list li svg { position: absolute; left: 0; top: 13px; }
  .hours { position: absolute; left: 0; width: 848px; top: 388px; text-align: center; font-weight: 600; font-size: 31px; line-height: 41px; color: var(--ink); }
  .hours .first { padding-left: 64px; }

  .contact-bar { position: absolute; left: 0; top: 1086px; width: 848px; height: 114px; background: var(--pink);
    font-family: "Roboto Condensed", sans-serif; color: var(--white); }
  .icon-disc { position: absolute; width: 48px; height: 48px; border-radius: 50%; background: var(--purple); display: flex; align-items: center; justify-content: center; }
  .contact-text { position: absolute; font-size: 18px; line-height: 25px; }
  .contact-text small { font-size: 13.5px; }
  .fb-dot { position: absolute; left: 22px; top: 74px; width: 26px; height: 26px; border-radius: 4px; background: #3b5998; }
</style>
</head>
<body>
<main class="flyer">
  <section class="hero" role="img" aria-label="Photo of a smiling girl with arms raised in front of a purple geometric backdrop with motivational words"></section>

  <div class="brand-card"><span>Ridge Lass<br>Crew</span></div>

  <div class="program-panel">
    <h1>A Girls Only After<br>School Program</h1>
    <p class="ages">11-14yrs</p>
    <p class="note">as OSHC is no longer available</p>
  </div>

  <div class="founder-band">
    <p>The Brainchild of Rebecca Folwin</p>
    <p>Ridge Lass Crew</p>
  </div>

  <section class="offer">
    <h2>We look to offer</h2>
    <ul class="offer-list">
      <li><svg width="16" height="16" viewBox="0 0 16 16"><circle cx="8" cy="8" r="6.5" fill="none" stroke="#fff" stroke-width="1.8"/><path d="M5 8.2l2 2 4-4" fill="none" stroke="#fff" stroke-width="1.8"/></svg>Daily meditation</li>
      <li><svg width="16" height="16" viewBox="0 0 16 16"><circle cx="8" cy="8" r="6.5" fill="none" stroke="#fff" stroke-width="1.8"/><path d="M5 8.2l2 2 4-4" fill="none" stroke="#fff" stroke-width="1.8"/></svg>Healthy snacks</li>
      <li><svg width="16" height="16" viewBox="0 0 16 16"><circle cx="8" cy="8" r="6.5" fill="none" stroke="#fff" stroke-width="1.8"/><path d="M5 8.2l2 2 4-4" fill="none" stroke="#fff" stroke-width="1.8"/></svg>Dedicated homework time</li>
      <li class="wrap"><svg width="16" height="16" viewBox="0 0 16 16"><circle cx="8" cy="8" r="6.5" fill="none" stroke="#fff" stroke-width="1.8"/><path d="M5 8.2l2 2 4-4" fill="none" stroke="#fff" stroke-width="1.8"/></svg>Organised group activity, led by qualified instructors<br>(yoga, fitness class, soccer etc.)</li>
      <li><svg width="16" height="16" viewBox="0 0 16 16"><circle cx="8" cy="8" r="6.5" fill="none" stroke="#fff" stroke-width="1.8"/><path d="M5 8.2l2 2 4-4" fill="none" stroke="#fff" stroke-width="1.8"/></svg>Regular guests speakers</li>
      <li><svg width="16" height="16" viewBox="0 0 16 16"><circle cx="8" cy="8" r="6.5" fill="none" stroke="#fff" stroke-width="1.8"/><path d="M5 8.2l2 2 4-4" fill="none" stroke="#fff" stroke-width="1.8"/></svg>SOCIAL MEDIA FREE ZONE</li>
    </ul>
    <div class="hours">
      <p class="first">Open every afternoon and during school holidays</p>
      <p>3-6pm Monday to Friday</p>
    </div>
  </section>

  <footer class="contact-bar">
    <div class="icon-disc" style="left:22px; top:16px;">
      <svg width="24" height="18" viewBox="0 0 24 18"><rect x="1" y="1" width="22" height="16" rx="2" fill="#fff"/><path d="M2 3l10 7 10-7" fill="none" stroke="#b768aa" stroke-width="2"/></svg>
    </div>
    <p class="contact-text" style="left:79px; top:10px;">e-Mail us<br>info@ridgelasscrew.example.au</p>
    <span class="fb-dot"></span>
    <p class="contact-text" style="left:73px; top:74px;">http://fb.example/ridgelasscrew</p>

    <div class="icon-disc" style="left:325px; top:26px; width:50px; height:60px;">
      <svg width="16" height="28" viewBox="0 0 16 28"><rect x="1" y="1" width="14" height="26" rx="3" fill="none" stroke="#fff" stroke-width="2"/><circle cx="8" cy="22" r="1.6" fill="#fff"/></svg>
    </div>
    <p class="contact-text" style="left:394px; top:30px;">Call Us Now<br><strong>0455817396</strong></p>

    <div class="icon-disc" style="left:574px; top:24px; width:52px; height:60px;">
      <svg width="20" height="28" viewBox="0 0 20 28"><path d="M10 1a9 9 0 0 1 9 9c0 7-9 17-9 17S1 17 1 10a9 9 0 0 1 9-9z" fill="#fff"/><circle cx="10" cy="10" r="3.5" fill="#b768aa"/></svg>
    </div>
    <p class="contact-text" style="left:652px; top:28px;">87 Pelham Pde,<br>Carrowby Heights<br><small>(across from Crestmoor Day Clinic)</small></p>
  </footer>
</main>
</body>
</html>
```